Beautiful design for wordpress

I need a beautiful, colourful and feminine website. My business is called 'The Velvet Lantern', and I sell crystals, books, CD's, pendulums and other metaphysical items. I also provide Reiki (energy healing).
I want this design to be eye catching and inspire happiness and joy in those who see it. And I would love to see the use of the logo and its colours :)
Please add these on the web design: Home, About, Online store, Blog

Industry/Entity Type

Business

Requirements
Must have
• Colourful and playful, must use the logo somewhere, have the words on a menu saying 'Home, Blog, Online store and about' (or similar to those)And the design must stand out!
Should not have
• grey, brown and other boring colours.

```html
<!DOCTYPE html>
<html lang="en">
<head>
<meta charset="utf-8">
<title>The Velvet Lantern — Crystals &amp; Gifts</title>
<link href="https://fonts.googleapis.com/css2?family=Open+Sans:wght@400;600;700&display=swap" rel="stylesheet">
<style>
  :root {
    --pink: #ee35b2;
    --pink-dark: #cf1f93;
    --pink-line: #f565c4;
    --white: #ffffff;
    --text: #6f6f6f;
    --text-dark: #555555;
    --green: #6f9a1f;
    --coral: #f26b7a;
    --brown: #8a5a35;
    --panel: #f7f7f4;
    --tag-yellow: #f6d77c;
    --tag-green: #c6dd8b;
    --tag-pink: #f7bfe0;
    --tag-blush: #f0ddd4;
    --tag-grey: #e2e2e2;
    --card-border: #f2d6cf;
    --footer: #2f2f2f;
    --footer-text: #c9c9c9;
    --social-blue: #2aa9e0;
    --social-teal: #1f8fc0;
    --social-orange: #f57d00;
  }
  * { margin: 0; padding: 0; box-sizing: border-box; }
  html, body { width: 885px; height: 1200px; overflow: hidden; }
  body { font-family: "Open Sans", sans-serif; background: var(--white); position: relative; color: var(--text); }

  .hero {
    position: absolute; left: 0; top: 0; width: 885px; height: 484px;
    background:
      radial-gradient(ellipse 170px 260px at 385px 250px, #fff4c8 0%, rgba(255,228,150,0.85) 35%, rgba(255,190,90,0) 100%),
      radial-gradient(ellipse 160px 60px at 420px 410px, #e58a5a 0%, rgba(229,138,90,0) 100%),
      linear-gradient(90deg, #c98a3a 0%, #f3a64a 25%, #f6b862 50%, #f3a64a 75%, #b9773a 100%);
  }
  .hero-ground { position: absolute; left: 215px; right: 0; bottom: 0; height: 6px; background: #3f7a1c; }
  .slide-arrow {
    position: absolute; top: 229px; width: 27px; height: 27px; background: var(--white);
    display: flex; align-items: center; justify-content: center;
  }
  .slide-arrow.prev { left: 0; }
  .slide-arrow.next { right: 0; }
  .slide-caption { position: absolute; right: 73px; top: 356px; text-align: right; }
  .caption-title {
    display: inline-block; background: var(--brown); color: var(--white);
    font-weight: 600; font-size: 36px; line-height: 49px; padding: 0 9px;
  }
  .caption-sub {
    display: block; margin-top: 3px; background: var(--brown); color: var(--white);
    font-weight: 600; font-size: 16px; line-height: 34px; padding: 0 10px; width: 133px; margin-left: auto;
  }

  .sidebar { position: absolute; left: 73px; top: 0; width: 142px; height: 484px; background: var(--pink); }
  .brand {
    height: 162px; background: var(--white); display: flex; flex-direction: column;
    align-items: center; justify-content: center; gap: 8px; border-bottom: 2px solid var(--pink-dark);
  }
  .brand-dot { width: 34px; height: 34px; border-radius: 50%; background: var(--pink); }
  .brand-name { font-size: 15px; font-weight: 700; color: var(--text-dark); text-align: center; line-height: 18px; }
  .nav a {
    display: flex; align-items: center; height: 31px; padding-left: 11px;
    color: var(--white); font-size: 11px; font-weight: 600; text-decoration: none;
    text-transform: uppercase; border-bottom: 1px solid var(--pink-line);
  }
  .nav a.current { background: linear-gradient(180deg, #d9269c, var(--pink-dark)); }
  .nav .leaf { width: 5px; height: 8px; background: var(--white); border-radius: 50%; transform: rotate(35deg); margin-right: 10px; }
  .search {
    position: absolute; left: 8px; top: 334px; width: 126px; height: 27px; background: var(--white);
    border-radius: 3px; display: flex; align-items: center; justify-content: space-between; padding: 0 6px 0 10px;
    font-size: 10px; color: var(--text-dark);
  }
  .sidebar-rule { position: absolute; left: 0; right: 0; top: 377px; height: 1px; background: var(--pink-line); }
  .info { position: absolute; left: 8px; display: flex; align-items: center; gap: 12px; color: var(--white); }
  .info.cart { top: 393px; }
  .info.call { top: 438px; }
  .info small { display: block; font-size: 9px; line-height: 11px; }
  .info strong { display: block; font-size: 14px; font-weight: 400; line-height: 18px; }

  .welcome { position: absolute; left: 118px; top: 510px; width: 650px; text-align: center; }
  .welcome h1 { font-size: 20px; font-weight: 400; color: var(--green); line-height: 28px; }
  .welcome p { margin-top: 9px; font-size: 10px; line-height: 17px; color: var(--text); }

  .divider { position: absolute; left: 73px; top: 631px; width: 739px; height: 1px; background: #e6e6e6; }
  .about {
    position: absolute; left: 73px; top: 634px; width: 739px; height: 157px; background: var(--panel);
  }
  .about h2 { position: absolute; left: 25px; top: 19px; font-size: 19px; font-weight: 400; color: var(--coral); }
  .about p { position: absolute; left: 25px; top: 50px; width: 455px; font-size: 10px; line-height: 17px; }
  .about-photo {
    position: absolute; right: 0; top: 0; width: 245px; height: 157px;
    background: radial-gradient(ellipse 110px 60px at 60% 50%, #ffffff 0%, #efe4dc 45%, rgba(247,247,244,0) 100%);
  }

  .we-sell { position: absolute; left: 165px; top: 829px; height: 28px; display: flex; align-items: center; gap: 5px; }
  .we-sell .label { font-size: 15px; color: var(--text); margin-right: 4px; }
  .tag { height: 28px; line-height: 28px; padding: 0 10px; font-size: 12px; color: var(--text-dark); position: relative; }
  .tag.crystals { background: var(--tag-yellow); }
  .tag.crystals::after {
    content: ""; position: absolute; left: 50%; bottom: -9px; margin-left: -8px;
    border-left: 8px solid transparent; border-right: 8px solid transparent; border-top: 9px solid var(--tag-yellow);
  }
  .tag.books { background: var(--tag-green); }
  .tag.cds { background: var(--tag-pink); }
  .tag.pendulums { background: var(--tag-yellow); }
  .tag.other { background: var(--tag-blush); }
  .tag.view-all { background: var(--tag-grey); height: 16px; line-height: 16px; font-size: 8px; padding: 0 6px; margin-left: 2px; text-transform: uppercase; }

  .products { position: absolute; left: 75px; top: 882px; display: flex; gap: 20px; }
  .product { width: 169px; height: 170px; border: 1px solid var(--card-border); text-align: center; padding-top: 7px; }
  .product-photo { width: 154px; height: 102px; margin: 0 auto; }
  .product h3 { font-size: 11px; font-weight: 400; color: var(--text); margin-top: 12px; }
  .product svg { margin-top: 5px; }

  .footer { position: absolute; left: 0; top: 1092px; width: 885px; height: 108px; background: var(--footer); }
  .footer-nav a { position: absolute; top: 22px; font-size: 10px; color: var(--footer-text); text-decoration: none; }
  .footer-nav a::before { content: "▪ "; font-size: 6px; vertical-align: 2px; }
  .footer-rule { position: absolute; left: 73px; top: 52px; width: 739px; height: 1px; background: #444; }
  .copyright { position: absolute; left: 75px; top: 72px; font-size: 10px; color: var(--footer-text); }
  .social { position: absolute; right: 76px; top: 66px; display: flex; gap: 9px; }
  .social span { width: 25px; height: 25px; border-radius: 50%; border: 2px solid #eee; }
</style>
</head>
<body>

<section class="hero" role="img" aria-label="Glowing lotus flower beneath a fountain of golden stars in a sunset sky">
  <div class="hero-ground"></div>
</section>
<a class="slide-arrow prev" aria-label="Previous slide">
  <svg width="14" height="16" viewBox="0 0 14 16"><path d="M11 1 L3 8 L11 15" fill="none" stroke="#444" stroke-width="3"/></svg>
</a>
<a class="slide-arrow next" aria-label="Next slide">
  <svg width="14" height="16" viewBox="0 0 14 16"><path d="M3 1 L11 8 L3 15" fill="none" stroke="#444" stroke-width="3"/></svg>
</a>
<div class="slide-caption">
  <span class="caption-title">Reiki</span>
  <span class="caption-sub">Energy Healing</span>
</div>

<aside class="sidebar">
  <div class="brand">
    <span class="brand-dot"></span>
    <span class="brand-name">The Velvet<br>Lantern</span>
  </div>
  <nav class="nav">
    <a class="current" href="#"><span class="leaf"></span>Home</a>
    <a href="#"><span class="leaf"></span>About</a>
    <a href="#"><span class="leaf"></span>Online Store</a>
    <a href="#"><span class="leaf"></span>Blog</a>
    <a href="#"><span class="leaf"></span>Contact Us</a>
  </nav>
  <div class="search">
    <span>Search</span>
    <svg width="18" height="18" viewBox="0 0 18 18"><circle cx="7.5" cy="7.5" r="5.5" fill="none" stroke="#999" stroke-width="2.5"/><path d="M11.5 11.5 L16 16" stroke="#999" stroke-width="3" stroke-linecap="round"/></svg>
  </div>
  <div class="sidebar-rule"></div>
  <div class="info cart">
    <svg width="22" height="20" viewBox="0 0 22 20"><path d="M7 7 L11 2 L15 7" fill="none" stroke="#fff" stroke-width="2"/><rect x="1" y="7" width="20" height="3" fill="#fff"/><path d="M3 11 H19 L17 19 H5 Z" fill="#fff"/></svg>
    <div><small>My Cart</small><strong>0 items</strong></div>
  </div>
  <div class="info call">
    <svg width="22" height="22" viewBox="0 0 22 22"><path d="M5 2 L8 7 L6 9 C7 12 10 15 13 16 L15 14 L20 17 L18 20 C10 20 2 12 2 4 Z" fill="#fff"/></svg>
    <div><small>Call us</small><strong>555 014 2287</strong></div>
  </div>
</aside>

<section class="welcome">
  <h1>Welcome to The Velvet Lantern</h1>
  <p>Sed nisl tortor, rutrum in scelerisque sit amet, luctus congue felis. Praesent a elit in lectus ultricies pulvinar at fringilla sem. Aliquam quis quam iaculis, lobortis augue nec, gravida mi. Quisque nec felis ac massa pellentesque malesuada. Quisque mollis aliquam lacus, ut lobortis tellus elementum in. Donec vel metus imperdiet, lobortis tellus vel, accumsan nunc.</p>
</section>

<div class="divider"></div>
<section class="about">
  <h2>About Reiki Service</h2>
  <p>Cras feugiat imperdiet mauris in blandit. Quisque venenatis faucibus leo, id adipiscing magna convallis quis. Curabitur consectetur, sem et tempus interdum, dui justo dignissim erat, nec volutpat eros lorem a libero. Donec quis porttitor augue, non ultricies massa. Ut diam lectus, varius eget ultrices non, accumsan id urna. Sed laoreet blandit bibendum. Fusce volutpat mi nec sapien imperdiet bibendum.</p>
  <div class="about-photo" role="img" aria-label="Two open hands with soft light glowing between them"></div>
</section>

<div class="we-sell">
  <span class="label">We Sell :</span>
  <span class="tag crystals">Crystals</span>
  <span class="tag books">Books</span>
  <span class="tag cds">CD's</span>
  <span class="tag pendulums">Pendulums</span>
  <span class="tag other">Other Metaphysical Items</span>
  <span class="tag view-all">View All</span>
</div>

<section class="products">
  <article class="product">
    <div class="product-photo" role="img" aria-label="Hands over a glowing crystal ball with red candles" style="background: radial-gradient(ellipse 50px 40px at 50% 80%, #fff2d8 0%, #e9a070 40%, #3a1410 100%);"></div>
    <h3>Morbi bibendum</h3>
    <svg width="20" height="17" viewBox="0 0 22 20"><path d="M7 7 L11 2 L15 7" fill="none" stroke="#777" stroke-width="2"/><rect x="1" y="7" width="20" height="3" fill="#777"/><path d="M3 11 H19 L17 19 H5 Z" fill="#777"/></svg>
  </article>
  <article class="product">
    <div class="product-photo" role="img" aria-label="Pile of purple and amber raw crystals" style="background: linear-gradient(135deg, #7a3fb0 0%, #c26ab8 35%, #e0a06a 60%, #6b2f8f 100%);"></div>
    <h3>Morbi bibendum</h3>
    <svg width="20" height="17" viewBox="0 0 22 20"><path d="M7 7 L11 2 L15 7" fill="none" stroke="#777" stroke-width="2"/><rect x="1" y="7" width="20" height="3" fill="#777"/><path d="M3 11 H19 L17 19 H5 Z" fill="#777"/></svg>
  </article>
  <article class="product">
    <div class="product-photo" role="img" aria-label="Hands holding a shimmering glass sphere on black" style="background: radial-gradient(circle 45px at 55% 40%, #d8e2e8 0%, #7c8c96 50%, #0c0c0c 100%);"></div>
    <h3>Morbi bibendum</h3>
    <svg width="20" height="17" viewBox="0 0 22 20"><path d="M7 7 L11 2 L15 7" fill="none" stroke="#777" stroke-width="2"/><rect x="1" y="7" width="20" height="3" fill="#777"/><path d="M3 11 H19 L17 19 H5 Z" fill="#777"/></svg>
  </article>
  <article class="product">
    <div class="product-photo" role="img" aria-label="Sparkling cut diamond on deep blue" style="background: radial-gradient(ellipse 60px 45px at 40% 45%, #d8f0f6 0%, #4a9ab0 45%, #0c3450 100%);"></div>
    <h3>Morbi bibendum</h3>
    <svg width="20" height="17" viewBox="0 0 22 20"><path d="M7 7 L11 2 L15 7" fill="none" stroke="#777" stroke-width="2"/><rect x="1" y="7" width="20" height="3" fill="#777"/><path d="M3 11 H19 L17 19 H5 Z" fill="#777"/></svg>
  </article>
</section>

<footer class="footer">
  <nav class="footer-nav">
    <a href="#" style="left:198px">Home</a>
    <a href="#" style="left:281px">About us</a>
    <a href="#" style="left:399px">Online store</a>
    <a href="#" style="left:533px">Blog</a>
    <a href="#" style="left:629px">Contact us</a>
  </nav>
  <div class="footer-rule"></div>
  <p class="copyright">Copyright &copy; 2014 The Velvet Lantern. &nbsp;All rights reserved.</p>
  <div class="social">
    <span style="background: var(--social-blue)"></span>
    <span style="background: var(--social-teal)"></span>
    <span style="background: var(--social-orange)"></span>
  </div>
</footer>

</body>
</html>
```